BOLD & MINIMALIST DESIGN NEEDED

We want a very bold but minimalistic business card design that is impactful and utilizes both sides of the business card. Our current logo is included for your use.

We want bold fonts and good use of negative space. We don't want the logo to overpower the design.

Target Market(s)

Professionals who are building new commercial buildings.

Industry/Entity Type

Construction

Contact Information for Business Card

Name, Title, email, office phone, cell phone, website

Font styles to use
Serif
Sans Serif

Requirements
Must have
• Bold design!

```html
<!DOCTYPE html>
<html lang="en">
<head>
<meta charset="utf-8">
<title>Ridgeline Design + Build – Business Card</title>
<link rel="stylesheet" href="https://fonts.googleapis.com/css2?family=Roboto:wght@400;700&display=swap">
<style>
  :root {
    --stage: #2b2b2b;
    --card-back: #151515;
    --card-back-mark: #2e2e2e;
    --card-front: #ffffff;
    --ink: #111111;
    --ink-soft: #3a3a3a;
    --accent: #7cc22a;
    --accent-light: #b9dd8c;
  }
  * { box-sizing: border-box; margin: 0; padding: 0; }
  html, body {
    width: 1200px; height: 694px; overflow: hidden;
    background: var(--stage);
    font-family: "Roboto", Arial, sans-serif;
  }
  .stage { position: relative; width: 1200px; height: 694px; }

  .card {
    position: absolute; top: 192px;
    width: 540px; height: 310px;
    border-radius: 18px; overflow: hidden;
  }

  /* Back side */
  .card--back { left: 40px; background: var(--card-back); }
  .back-wordmark {
    position: absolute; left: 0; right: 0; top: 118px;
    text-align: center; color: var(--card-back-mark);
    font-weight: 700; line-height: 1.05;
  }
  .back-wordmark .name { font-size: 44px; letter-spacing: 1px; }
  .back-wordmark .tag { font-size: 16px; letter-spacing: 6px; }

  /* Front side */
  .card--front { left: 620px; background: var(--card-front); }
  .front-art { position: absolute; inset: 0; width: 540px; height: 310px; }
  .front-art .arc { fill: var(--ink); }

  .person {
    position: absolute; top: 26px; right: 34px; text-align: right;
  }
  .person__name { color: var(--accent); font-weight: 700; font-size: 22px; line-height: 1.1; }
  .person__title { color: var(--ink); font-size: 13px; margin-top: 2px; }
  .accent-bar {
    position: absolute; top: 24px; right: 0; width: 9px; height: 44px;
    background: var(--accent);
  }

  .wordmark {
    position: absolute; left: 36px; top: 86px;
    display: flex; align-items: flex-start; gap: 10px;
    color: var(--ink); font-weight: 700; line-height: 1;
  }
  .wordmark__square { width: 14px; height: 14px; background: var(--accent); margin-top: 8px; }
  .wordmark__name { font-size: 38px; letter-spacing: 0.5px; }
  .wordmark__tag { font-size: 14px; letter-spacing: 6px; margin-top: 6px; }

  .contacts {
    position: absolute; left: 40px; top: 164px;
    list-style: none; color: var(--ink-soft); font-size: 13px;
  }
  .contacts li { display: flex; align-items: center; gap: 10px; height: 20px; }
  .contacts svg { width: 12px; height: 12px; fill: var(--ink); flex: none; }
  .address {
    position: absolute; left: 62px; top: 250px;
    color: var(--ink-soft); font-size: 13px; line-height: 17px;
  }
</style>
</head>
<body>
<main class="stage">

  <section class="card card--back" aria-label="Card back">
    <div class="back-wordmark">
      <div class="name">RIDGELINE</div>
      <div class="tag">DESIGN + BUILD</div>
    </div>
  </section>

  <section class="card card--front" aria-label="Card front">
    <svg class="front-art" viewBox="0 0 540 310" aria-hidden="true">
      <defs>
        <linearGradient id="symbolFill" x1="0" y1="0" x2="1" y2="1">
          <stop offset="0" stop-color="var(--accent-light)"/>
          <stop offset="1" stop-color="var(--accent)"/>
        </linearGradient>
      </defs>
      <path class="arc" d="M340 310 Q400 170 540 132 L540 150 Q430 190 372 310 Z"/>
    </svg>
    <svg style="position:absolute;left:350px;top:80px;width:150px;height:140px" viewBox="0 0 150 140" role="img" aria-label="Company symbol area">
      <rect width="150" height="140" rx="4" fill="url(#symbolFill)"/>
    </svg>

    <div class="accent-bar"></div>
    <div class="person">
      <div class="person__name">Daniel Carter</div>
      <div class="person__title">Owner</div>
    </div>

    <div class="wordmark">
      <span class="wordmark__square"></span>
      <div>
        <div class="wordmark__name">RIDGELINE</div>
        <div class="wordmark__tag">DESIGN + BUILD</div>
      </div>
    </div>

    <ul class="contacts">
      <li>
        <svg viewBox="0 0 24 24" aria-hidden="true"><rect x="6" y="1" width="12" height="22" rx="2"/></svg>
        044-123 456 789
      </li>
      <li>
        <svg viewBox="0 0 24 24" aria-hidden="true"><path d="M6.6 10.8a15 15 0 0 0 6.6 6.6l2.2-2.2a1 1 0 0 1 1-.25 11 11 0 0 0 3.6.6 1 1 0 0 1 1 1V20a1 1 0 0 1-1 1A17 17 0 0 1 3 4a1 1 0 0 1 1-1h3.5a1 1 0 0 1 1 1 11 11 0 0 0 .6 3.6 1 1 0 0 1-.25 1z"/></svg>
        044-123 456 789
      </li>
      <li>
        <svg viewBox="0 0 24 24" aria-hidden="true"><path d="M2 5h20v14H2z M2 5l10 8 10-8" /></svg>
        info@webname.com
      </li>
      <li>
        <svg viewBox="0 0 24 24" aria-hidden="true"><circle cx="12" cy="12" r="10"/></svg>
        www.website.com
      </li>
    </ul>

    <p class="address">Address line goes here<br>45452, Country name</p>
  </section>

</main>
</body>
</html>
```